New Business Card Design Project

We require a business card design for Vexalund, a newly established Indian company.
Our focus is on the development, manufacturing, and export of a diverse array of pharmaceutical products on a global scale. The card should convey a professional appearance, as our primary markets are in Africa, China, and Southeast Asian nations.
We envision a two-sided business card, with the reverse side dedicated to a logo set against a solid color or an elegantly designed pattern. The corners should be rounded. We would appreciate seeing both horizontal and vertical design options. We trust the designer to utilize their expertise in creating this design.

The content for the business card is included in the attached Word file.

Target Market(s)

Our primary markets are in Africa, China, and Southeast Asian, Latin America, Maldives, Sri Lanka

Industry/Entity Type

Pharmaceutical Manufacturing and Export

Contact Information for Business Card

Colors

Designer to choose colors to be used in the design.

Requirements
Must have
• The reverse side of the business card features solely the logo along with the tagline, "Remedies of Life."
Should not have
• The logo should not exceed two instances, encompassing both the front and back sides of the card.

```html
<!DOCTYPE html>
<html lang="en">
<head>
<meta charset="utf-8">
<title>Vexalund Business Card</title>
<link href="https://fonts.googleapis.com/css2?family=Poppins:wght@400;500;700&display=swap" rel="stylesheet">
<style>
  :root {
    --brand-blue: #27a8e0;
    --brand-coral: #ef604f;
    --paper: #ffffff;
    --ink: #2b2b2b;
    --backdrop: #e9ebee;
  }
  * { box-sizing: border-box; margin: 0; padding: 0; }
  html, body { width: 1200px; height: 900px; overflow: hidden; }
  body {
    background: var(--backdrop);
    font-family: "Poppins", sans-serif;
    position: relative;
  }
  .card {
    position: absolute;
    left: 270px;
    width: 660px;
    height: 377px;
    border-radius: 22px;
    overflow: hidden;
    box-shadow: 0 6px 18px rgba(0,0,0,0.15);
  }

  /* Reverse side */
  .card-back {
    top: 40px;
    background: var(--brand-blue);
  }
  .back-brand {
    position: absolute;
    left: 0;
    right: 0;
    top: 50%;
    transform: translateY(-50%);
    display: flex;
    flex-direction: column;
    align-items: center;
    gap: 10px;
  }
  .back-brand .lockup {
    display: flex;
    align-items: center;
    gap: 18px;
  }
  .back-brand .dot {
    width: 34px; height: 34px;
    border-radius: 50%;
    background: var(--brand-coral);
  }
  .back-brand .wordmark {
    color: var(--paper);
    font-weight: 700;
    font-size: 64px;
    line-height: 1;
    letter-spacing: 0.5px;
  }
  .back-brand .tagline {
    color: var(--paper);
    font-weight: 500;
    font-size: 20px;
    letter-spacing: 4px;
    text-transform: uppercase;
    padding-left: 52px;
  }

  /* Front side */
  .card-front {
    top: 483px;
    background: var(--paper);
  }
  .front-brand {
    position: absolute;
    right: 50px;
    top: 64px;
    display: flex;
    align-items: center;
    gap: 12px;
  }
  .front-brand .dot {
    width: 22px; height: 22px;
    border-radius: 50%;
    background: var(--brand-coral);
  }
  .front-brand .wordmark {
    color: var(--brand-blue);
    font-weight: 700;
    font-size: 46px;
    line-height: 1;
  }
  .person {
    position: absolute;
    left: 62px;
    top: 122px;
  }
  .person .name {
    color: var(--brand-blue);
    font-weight: 700;
    font-size: 27px;
    line-height: 1.15;
  }
  .person .role {
    color: var(--ink);
    font-size: 15px;
    margin-left: 28px;
    line-height: 1.3;
  }
  .rule {
    position: absolute;
    left: 70px;
    right: 40px;
    top: 185px;
    height: 1.5px;
    background: var(--brand-blue);
  }
  .contacts {
    position: absolute;
    left: 86px;
    top: 200px;
    list-style: none;
  }
  .contacts li {
    display: flex;
    align-items: center;
    gap: 10px;
    color: var(--ink);
    font-size: 17px;
    line-height: 28px;
  }
  .contacts svg { width: 14px; height: 14px; fill: var(--brand-coral); flex: none; }
  .address {
    position: absolute;
    right: 42px;
    top: 200px;
    text-align: right;
    color: var(--ink);
    font-size: 16px;
    line-height: 1.5;
  }
  .edge-bands {
    position: absolute;
    left: 0; bottom: 0;
    width: 660px; height: 60px;
  }
</style>
</head>
<body>

  <section class="card card-back" aria-label="Card reverse">
    <div class="back-brand">
      <div class="lockup">
        <span class="dot"></span>
        <span class="wordmark">Vexalund</span>
      </div>
      <p class="tagline">Remedies of Life</p>
    </div>
  </section>

  <section class="card card-front" aria-label="Card front">
    <div class="front-brand">
      <span class="dot"></span>
      <span class="wordmark">Vexalund</span>
    </div>

    <div class="person">
      <p class="name">Arjun K. Rathore</p>
      <p class="role">CEO</p>
    </div>

    <div class="rule"></div>

    <ul class="contacts">
      <li>
        <svg viewBox="0 0 24 24" aria-hidden="true"><path d="M6.6 10.8a15.1 15.1 0 0 0 6.6 6.6l2.2-2.2a1 1 0 0 1 1-.25 11.4 11.4 0 0 0 3.6.57 1 1 0 0 1 1 1V20a1 1 0 0 1-1 1A17 17 0 0 1 3 4a1 1 0 0 1 1-1h3.5a1 1 0 0 1 1 1c0 1.25.2 2.45.57 3.6a1 1 0 0 1-.25 1z"/></svg>
        +919800012345
      </li>
      <li>
        <svg viewBox="0 0 24 24" aria-hidden="true"><path d="M2 6a2 2 0 0 1 2-2h16a2 2 0 0 1 2 2v12a2 2 0 0 1-2 2H4a2 2 0 0 1-2-2zm2 .5V7l8 5 8-5v-.5z"/></svg>
        arathore@vexalund.com
      </li>
      <li>
        <svg viewBox="0 0 24 24" aria-hidden="true"><circle cx="12" cy="12" r="10"/></svg>
        www.vexalund.com
      </li>
    </ul>

    <p class="address">14, Sarovar Colony, 442001<br>Wardha, India</p>

    <svg class="edge-bands" viewBox="0 0 660 60" aria-hidden="true">
      <polygon points="0,46 428,46 442,30 416,60 0,60" fill="var(--brand-blue)"/>
      <polygon points="450,60 474,30 660,30 660,60" fill="var(--brand-coral)"/>
    </svg>
  </section>

</body>
</html>
```